Namecard for wristwatch company

I run a watch company named Varnik which just launched our first watch. I need a namecard design that is unique and something very different. It should be the same size or smaller than the usual cards. It will be printed on the usual paper as metal/wood are nice but might be too expensive.
I have attached some photos of my watch and the company logo as well.

Target Market(s)
Watch collectors, young professionals
Industry/Entity Type
It Company
Look and feel

```html
<!DOCTYPE html>
<html lang="en">
<head>
<meta charset="utf-8">
<title>Varnik Namecard</title>
<link rel="stylesheet" href="https://fonts.googleapis.com/css2?family=Orbitron:wght@500&family=Exo+2:wght@400;600&display=swap">
<style>
:root{
  --stage:#ecebe8;
  --paper:#ffffff;
  --paper-shade:#f1f2f3;
  --frame-grey:#d3d5d7;
  --sky:#0aafe9;
  --slate:#4a4b4f;
  --ink:#3c3d40;
  --ring:#55575b;
}
*{box-sizing:border-box;margin:0;padding:0}
html,body{width:1057px;height:1200px;overflow:hidden}
body{background:var(--stage);font-family:"Exo 2",sans-serif;position:relative}
.card{position:absolute;top:268px;width:380px;height:665px;box-shadow:0 10px 30px rgba(0,0,0,.18)}
.card--front{left:110px;background:var(--frame-grey);padding:12px}
.card--back{left:567px;background:var(--sky);padding:16px}
.card__face{position:relative;width:100%;height:100%;background:linear-gradient(160deg,var(--paper) 40%,var(--paper-shade));overflow:hidden}
.brand{position:absolute;left:0;right:0;display:flex;align-items:center;justify-content:center;gap:12px}
.brand__ring{width:30px;height:30px;border:4px solid var(--ring);border-radius:50%}
.brand__name{font-family:"Exo 2",sans-serif;font-weight:600;font-size:34px;color:var(--sky);letter-spacing:1px}
.card--front .brand{top:96px}
.card--back .brand{top:290px}
.holder{position:absolute;left:34px;top:205px}
.holder__name{font-family:"Orbitron",sans-serif;font-weight:500;font-size:24px;color:var(--ink);letter-spacing:1px}
.holder__role{font-size:12px;letter-spacing:2px;color:var(--ink);margin-top:4px}
.contacts{position:absolute;left:0;right:0;top:290px;height:245px;background:var(--sky);padding:30px 34px;display:flex;flex-direction:column;gap:22px}
.contact{display:flex;align-items:center;gap:14px;color:#fff;font-size:14px;letter-spacing:.5px}
.contact__icon{width:24px;height:24px;border-radius:50%;background:#fff;display:flex;align-items:center;justify-content:center;flex:none}
.address{position:absolute;left:0;right:0;top:535px;height:70px;background:var(--slate);display:flex;align-items:center;gap:14px;padding:0 34px;color:#fff;font-size:14px}
</style>
</head>
<body>
<section class="card card--front">
  <div class="card__face">
    <div class="brand"><span class="brand__ring"></span><span class="brand__name">Varnik</span></div>
    <div class="holder">
      <p class="holder__name">ZELOS VARNIK</p>
      <p class="holder__role">GENERAL MANAGER</p>
    </div>
    <div class="contacts">
      <p class="contact"><span class="contact__icon"><svg width="14" height="14" viewBox="0 0 24 24"><path fill="#4a4b4f" d="M6.6 10.8a15 15 0 0 0 6.6 6.6l2.2-2.2a1 1 0 0 1 1-.25 11 11 0 0 0 3.6.6 1 1 0 0 1 1 1V20a1 1 0 0 1-1 1A17 17 0 0 1 3 4a1 1 0 0 1 1-1h3.5a1 1 0 0 1 1 1 11 11 0 0 0 .6 3.6 1 1 0 0 1-.25 1z"/></svg></span>012 555 0147</p>
      <p class="contact"><span class="contact__icon"><svg width="14" height="14" viewBox="0 0 24 24"><rect x="6" y="2" width="12" height="20" rx="2" fill="none" stroke="#4a4b4f" stroke-width="2.4"/><circle cx="12" cy="18" r="1.4" fill="#4a4b4f"/></svg></span>012 555 0148</p>
      <p class="contact"><span class="contact__icon"><svg width="14" height="14" viewBox="0 0 24 24"><rect x="2" y="5" width="20" height="14" rx="1.5" fill="#4a4b4f"/><path d="M3 6l9 7 9-7" fill="none" stroke="#fff" stroke-width="1.8"/></svg></span>hello@varnik.co</p>
      <p class="contact"><span class="contact__icon"><svg width="14" height="14" viewBox="0 0 24 24"><circle cx="12" cy="12" r="9" fill="none" stroke="#4a4b4f" stroke-width="2.2"/><path d="M3 12h18M12 3c3 3 3 15 0 18M12 3c-3 3-3 15 0 18" fill="none" stroke="#4a4b4f" stroke-width="1.6"/></svg></span>www.varnikwatch.co</p>
    </div>
    <div class="address">
      <span class="contact__icon"><svg width="14" height="14" viewBox="0 0 24 24"><path fill="#4a4b4f" d="M12 2a7 7 0 0 0-7 7c0 5 7 13 7 13s7-8 7-13a7 7 0 0 0-7-7zm0 9.5A2.5 2.5 0 1 1 12 6.5a2.5 2.5 0 0 1 0 5z"/></svg></span>
      <span>27 Harbor Lane, 4th Floor, Suite 9</span>
    </div>
  </div>
</section>
<section class="card card--back">
  <div class="card__face">
    <div class="brand"><span class="brand__ring"></span><span class="brand__name">Varnik</span></div>
  </div>
</section>
</body>
</html>
```